Moxy Fen needs some awesome stationary

Do you have what it takes to get my brand? You either do or you don't, have a crack at a design and you my just win my business.

I don't want to waste your or my time, so put your creative genius on either a business card or envelope.

I however need a package of stationary that follows the same brand. I will message you to complete the remaining should I like your first submission.

Here is what I need, have a go!

Basically I need the following for my small business based in melbourne.
- Letterhead (printer ready and MS Word)
- Business Card
- Compliments Slip
- Envelope
- Proposal Cover Page (MS Word only)
- Presentation Folder
- Marbled Fox Cards
- Student Name Tent
- Index Cards
- Vell-Ka

I am establishing the brand and it must be modern, professional but also relaxed; that is not formal and not corporate. It represents a company are leaders, but small enough to care and operate like a bunch of friends. We are bringing people and conversations back to business, and turfing out all the bureaucracy and crazy and wasteful procedures. Its about "lets talk and figure it out together and find even better ways".

Target Market(s)

Mainly companies that build software products, but Agile practices are used in many other industries (even graphic design projects)

Industry/Entity Type

Information Technology

Font styles to use
Sans Serif

Colors
3176b5
aaaaaa

Requirements
Must have
• I like curves and circles and not boxes or rectangles.
• I want a colour rich design with my brand colours, but it must be balanced.
• I want more modern than traditional, but simple modern
Should not have
• Not corporate
• Please don't waste my time if your not going to think about it.
• Don't mess with my primary logo
• Don't change my colours
• Don't overlay logo on image

```html
<!DOCTYPE html>
<html lang="en">
<head>
<meta charset="utf-8">
<title>Moxy Fen – Business Card</title>
<link href="https://fonts.googleapis.com/css2?family=Open+Sans:wght@400;600;700&display=swap" rel="stylesheet">
<style>
  :root {
    --brand-blue: #1553a3;
    --brand-blue-light: #3176b5;
    --brand-grey: #aaaaaa;
    --paper: #ffffff;
    --backdrop: #e9ebee;
  }
  * { box-sizing: border-box; margin: 0; padding: 0; }
  html, body { width: 1200px; height: 800px; overflow: hidden; }
  body {
    background: var(--backdrop);
    font-family: "Open Sans", Arial, sans-serif;
    position: relative;
  }
  .card {
    position: absolute;
    top: 244px;
    width: 520px;
    height: 312px;
    overflow: hidden;
    box-shadow: 0 6px 18px rgba(0,0,0,.18);
  }
  .card--back {
    left: 50px;
    background: linear-gradient(110deg, var(--brand-blue) 0%, var(--brand-blue-light) 100%);
  }
  .card--front { left: 630px; background: var(--paper); }

  /* back */
  .back-brand {
    position: absolute; left: 0; right: 0; top: 118px;
    display: flex; align-items: center; justify-content: center; gap: 14px;
  }
  .brand-dot { width: 44px; height: 44px; border-radius: 50%; background: var(--brand-grey); }
  .back-brand .brand-name { color: var(--paper); font-size: 40px; font-weight: 700; letter-spacing: .5px; }

  /* front */
  .front-band {
    position: absolute; left: 0; right: 0; top: 122px; bottom: 0;
    background: linear-gradient(110deg, var(--brand-blue) 0%, var(--brand-blue-light) 100%);
  }
  .accent-square { position: absolute; left: 128px; top: 0; width: 18px; height: 12px; background: var(--brand-blue); }
  .accent-notch { position: absolute; left: 104px; top: 118px; width: 40px; height: 12px; background: var(--paper); }
  .front-brand {
    position: absolute; left: 26px; top: 40px;
    display: flex; align-items: center; gap: 8px;
  }
  .front-brand .brand-dot { width: 20px; height: 20px; background: var(--brand-blue); }
  .front-brand .brand-name { color: var(--brand-blue); font-size: 18px; font-weight: 700; }
  .name-plate {
    position: absolute; right: 14px; top: 76px; width: 262px; height: 48px;
    background: var(--brand-blue); color: var(--paper);
    padding: 6px 14px 0 0; text-align: right;
  }
  .person-name { font-size: 17px; font-weight: 700; font-variant: small-caps; letter-spacing: 1.5px; line-height: 1.1; }
  .person-title { font-size: 11px; font-variant: small-caps; letter-spacing: .6px; }
  .contact-list {
    position: absolute; right: 22px; top: 158px;
    list-style: none; color: var(--paper); font-size: 11px; line-height: 19px; text-align: right;
  }
  .contact-list li { display: flex; justify-content: flex-end; align-items: center; gap: 10px; }
  .contact-list .hotline { font-weight: 700; }
  .contact-list svg { width: 11px; height: 11px; flex: none; fill: var(--paper); }
  .contact-list .spacer { width: 11px; flex: none; }
</style>
</head>
<body>
  <section class="card card--back" aria-label="Business card back">
    <div class="back-brand">
      <span class="brand-dot"></span>
      <span class="brand-name">Moxy Fen</span>
    </div>
  </section>

  <section class="card card--front" aria-label="Business card front">
    <div class="front-band"></div>
    <span class="accent-square"></span>
    <span class="accent-notch"></span>
    <div class="front-brand">
      <span class="brand-dot"></span>
      <span class="brand-name">Moxy Fen</span>
    </div>
    <div class="name-plate">
      <p class="person-name">Dana Quill</p>
      <p class="person-title">CEO, Professional Scrum Trainer</p>
    </div>
    <ul class="contact-list">
      <li class="hotline">1300MOXYFN
        <svg viewBox="0 0 12 12"><path d="M2 1h2.5l1 2.5-1.3 1a6 6 0 0 0 3.3 3.3l1-1.3 2.5 1V10a1 1 0 0 1-1 1A9 9 0 0 1 1 2a1 1 0 0 1 1-1z"/></svg></li>
      <li>+61 400 218 376
        <svg viewBox="0 0 12 12"><path d="M3.5 0h5a1 1 0 0 1 1 1v10a1 1 0 0 1-1 1h-5a1 1 0 0 1-1-1V1a1 1 0 0 1 1-1zm0 1.5v8h5v-8z"/></svg></li>
      <li>dana@moxyfen.com.au
        <svg viewBox="0 0 12 12"><path d="M0 2h12v8H0zm1 1v.3l5 3.2 5-3.2V3z"/></svg></li>
      <li>www.moxyfen.com.au
        <svg viewBox="0 0 12 12"><path d="M6 0a6 6 0 1 0 0 12A6 6 0 0 0 6 0zm0 1.5a4.5 4.5 0 1 1 0 9 4.5 4.5 0 0 1 0-9zm0 2a2.5 2.5 0 1 0 0 5 2.5 2.5 0 0 0 0-5z"/></svg></li>
      <li>PO Box 4410, Ferncliff Lower,
        <svg viewBox="0 0 12 12"><path d="M6 0a4 4 0 0 1 4 4c0 3-4 8-4 8S2 7 2 4a4 4 0 0 1 4-4zm0 2.5a1.5 1.5 0 1 0 0 3 1.5 1.5 0 0 0 0-3z"/></svg></li>
      <li>VIC 3199, Australia <span class="spacer"></span></li>
    </ul>
  </section>
</body>
</html>
```